Visitenkarten/Briefpaier/Kassenkassenbelege für Juwelier
Zielgruppe
Mittelständischer Juwelier mit zwei Filialen. Klassischer Schmuck, Uhren und Modeschmuck
Aufgabenstellung
Es müssen für zwei Geschäfte Visitenkarten, Briefpapier (A4) und Kassenkassenbelege (A6) erstellt werden. Logo und Typo im Anhang. Ein Farbkonzept besteht noch nicht. Die Idee geht in Richtung Bordeaux-Rot.
Generell:
(1) Sieht erstmal nach viel Beschreibung aus, bitte nicht entmutigen lassen, sind zu 90% nur austauschbare Inhalts-/Kontaktdaten.
(2) Für meine Zwecke reicht es vollkommen aus, wenn bei den Vorschlägen zur Arbeitsersparnis erstmal nur mit einer Adresse gearbeitet wird. Wenn ich dann den zutreffenden Designvorschlag gefunden habe, können wir die zweite Adresse in dem ersten Format umsetzen. Ich denke das spart Zeit und Nerven.
(3) Bitte Angaben wie "Tel.:" oder "USt.- ID:" nicht wörtlich nehmen, es soll dabei klar sein worum es geht; wenn "Telefon" ausgeschrieben besser aussieht, bitte in der optisch ansprechenderen Form verwenden.
(4) Bei Fragen, bitte fragen!
(5) Viel Spass bei dem Projekt - Ich freu' mich auf die Vorschläge!
Visitenkarten(1):
Juwelier Brenneck GmbH
www.juwelier-brenneck-beispiel.de
Visitenkarten(2):
Visitenkarten(generell):
(1) Die einzelnen Daten können durch Hervorhebungen wie Adresse, Kontakt, Online/Internet unterteilt bzw. hervorgehoben werden.
(2) Die Visitenkarten sollen farbig gedruckt werden; geplant ist weiß als Hintergrund ist aber nicht zwingend bei einer guten anderen Idee
Briefpapier:
(1)Absender im Adressfeld für DIN-lang Briefumschläge mit Fenster:
(2)Informationen im Footer/Seitenbereich:
Juwelier Brenneck Gmb..

```html
<!DOCTYPE html>
<html lang="de">
<head>
<meta charset="utf-8">
<title>Juwelier Brenneck – Geschäftsausstattung</title>
<link rel="stylesheet" href="https://fonts.googleapis.com/css2?family=Source+Sans+3:wght@400;600;700&display=swap">
<style>
:root{
  --bordeaux:#6b0000;
  --grey:#8a868c;
  --text:#333;
  --rule:#cfcfcf;
  --stage:#e0e0e2;
  --paper:#fff;
  --tint-red:#eadcdc;
  --tint-grey:#e4e4e6;
}
*{box-sizing:border-box;margin:0;padding:0}
html,body{width:849px;height:1200px;overflow:hidden}
body{background:var(--stage);font-family:"Source Sans 3",sans-serif;font-weight:400;color:var(--text);position:relative}
.sheet{position:absolute;background:var(--paper);box-shadow:2px 2px 3px rgba(0,0,0,.3);overflow:hidden}
.red{color:var(--bordeaux)}
.grey{color:var(--grey)}
b{font-weight:700}

/* brand name block (replaces mark) */
.brand{display:flex;align-items:center;justify-content:center;gap:.35em;font-weight:700;letter-spacing:.04em;text-transform:uppercase;color:var(--bordeaux)}
.brand::before{content:"";width:.7em;height:.7em;background:currentColor;flex:none}
.brand--grey{color:var(--grey)}

/* business cards */
.card{width:171px;height:111px}
.card .brand{position:absolute;left:0;right:0;font-size:13px}
.card--front .brand{top:46px}
.card--back .brand{top:30px;font-size:10px}
.card__contact{position:absolute;left:0;right:0;top:84px;text-align:center;font-size:4.2px;line-height:6.4px;color:var(--grey)}
.card__contact b{color:var(--bordeaux)}

/* decorative back sheets */
.decor{position:absolute;right:0;bottom:0}

/* receipts */
.receipt{width:149px;height:212px}
.receipt .brand{position:absolute;left:0;right:0;top:32px;font-size:7.5px}
.receipt__lines{position:absolute;left:13px;right:13px;top:58px}
.receipt__lines span{display:block;height:8.2px;border-bottom:.5px solid var(--rule)}
.receipt--alt .receipt__lines span{border-color:#e39a9a}
.receipt__sum{position:absolute;right:13px;top:152px;font-size:3px;line-height:8px;font-weight:600;text-align:right}
.receipt__sum span{display:inline-block;width:36px;border-bottom:.5px solid var(--rule);margin-left:4px}
.receipt__note{position:absolute;left:0;right:0;top:173px;text-align:center;font-size:3px;line-height:3.8px;font-weight:600;color:var(--bordeaux)}
.receipt__foot{position:absolute;left:0;right:0;top:194px;text-align:center;font-size:3.4px;line-height:5px;color:var(--grey)}
.receipt__foot b{color:var(--bordeaux)}

/* letterhead */
.letter{width:424px;height:595px;transform-origin:0 0}
.letter .brand{position:absolute;left:0;right:0;top:62px;font-size:15px}
.letter--compact .brand{justify-content:flex-end;right:14px;left:auto}
.letter__fold{position:absolute;left:0;width:10px;height:1px;background:var(--grey)}
.letter__sender{position:absolute;left:49px;top:109px;font-size:4.4px;color:var(--grey)}
.letter__sender b{color:var(--bordeaux)}
.letter__address{position:absolute;left:49px;top:127px;font-size:6.3px;line-height:8.6px;color:var(--grey)}
.letter__address .red{display:block}
.letter__address .gap{height:8.6px}
.letter__side{position:absolute;left:325px;top:107px;font-size:4.5px;line-height:6px;color:var(--grey)}
.letter__side .head{color:var(--grey);font-weight:600;letter-spacing:.03em}
.letter__side .red{color:var(--bordeaux)}
.letter__side .gap{height:5px}
.letter__date{position:absolute;left:325px;top:233px;font-size:4.5px;color:var(--grey)}
.letter__body{position:absolute;left:49px;top:240px;width:252px;font-size:6.6px;line-height:8.85px;font-weight:400;color:#222}
.letter__body p{margin-bottom:8.85px}
.letter__body .close{margin-top:14px}
.letter__foot{position:absolute;left:0;right:0;top:574px;text-align:center;font-size:5px;line-height:7.8px;color:var(--grey)}
.letter__foot b{color:var(--bordeaux);font-weight:600}
</style>
</head>
<body>

<!-- business cards -->
<div class="sheet card card--front" style="left:31px;top:195px">
  <div class="brand">Juwelier Brenneck</div>
</div>
<div class="sheet card card--front" style="left:216px;top:195px">
  <div class="brand brand--grey">Juwelier Brenneck</div>
</div>
<div class="sheet card card--back" style="left:31px;top:316px">
  <div class="brand">Juwelier Brenneck</div>
  <div class="card__contact">
    <b>JUWELIER BRENNECK GMBH</b> | Lindenallee 12 | 45100 Beispielstadt<br>
    <b>T</b> 0201 00 11 22 | <b>F</b> 0201 00 11 33<br>
    <b>M</b> info@juwelier-brenneck-beispiel.de | <b>W</b> www.juwelier-brenneck-beispiel.de
  </div>
</div>
<div class="sheet card card--back" style="left:216px;top:316px">
  <div class="brand brand--grey">Juwelier Brenneck</div>
  <div class="card__contact">
    <b>JUWELIER BRENNECK GMBH</b> | Gartenweg 8 | 45200 Nebenstadt<br>
    <b>T</b> 0202 00 44 5 | <b>F</b> 0202 00 55 66<br>
    <b>M</b> brenneck@juwelier-brenneck-beispiel.de | <b>W</b> www.juwelier-brenneck-beispiel.de
  </div>
</div>

<!-- receipts, set 1 -->
<div class="sheet receipt" style="left:446px;top:136px">
  <div class="decor" role="img" aria-label="Große Diamant-Linienzeichnung in Bordeaux" style="width:90px;height:120px;background:var(--tint-red)"></div>
</div>
<div class="sheet receipt" style="left:402px;top:117px">
  <div class="brand">Juwelier Brenneck</div>
  <div class="receipt__lines"><span></span><span></span><span></span><span></span><span></span><span></span><span></span><span></span><span></span><span></span></div>
  <div class="receipt__sum">19 % MwSt.<span></span><br>Gesamt<span></span></div>
  <div class="receipt__note">Bei Umtausch oder Reklamation bitte Beleg vorlegen.<br>Barauszahlung ganz oder teilweise ausgeschlossen</div>
  <div class="receipt__foot"><b>JUWELIER BRENNECK GMBH</b> | Lindenallee 12 | 45100 Beispielstadt<br><b>T</b> 0201 00 11 22 | <b>F</b> 0201 00 11 33<br><b>M</b> info@juwelier-brenneck-beispiel.de | <b>W</b> www.juwelier-brenneck-beispiel.de</div>
</div>

<!-- receipts, set 2 -->
<div class="sheet receipt" style="left:660px;top:136px">
  <div class="decor" role="img" aria-label="Große Diamant-Linienzeichnung in Grau" style="width:90px;height:120px;background:var(--tint-grey)"></div>
</div>
<div class="sheet receipt receipt--alt" style="left:627px;top:117px">
  <div class="brand brand--grey">Juwelier Brenneck</div>
  <div class="receipt__lines"><span></span><span></span><span></span><span></span><span></span><span></span><span></span><span></span><span></span><span></span></div>
  <div class="receipt__sum">19 % MwSt.<span></span><br>Gesamt<span></span></div>
  <div class="receipt__note">Bei Umtausch oder Reklamation bitte Beleg vorlegen.<br>Barauszahlung ganz oder teilweise ausgeschlossen</div>
  <div class="receipt__foot"><b>JUWELIER BRENNECK GMBH</b> | Gartenweg 8 | 45200 Nebenstadt<br><b>T</b> 0202 00 44 5 | <b>F</b> 0202 00 55 66<br><b>M</b> info@juwelier-brenneck-beispiel.de | <b>W</b> www.juwelier-brenneck-beispiel.de</div>
</div>

<!-- full letterhead pair (drawn first so the compact pair sits above it) -->
<div class="sheet letter" style="left:145px;top:564px;height:600px">
  <div class="decor" role="img" aria-label="Große Diamant-Linienzeichnung in Bordeaux" style="width:424px;height:460px;background:var(--tint-red)"></div>
</div>
<div class="sheet letter" style="left:16px;top:478px">
  <div class="brand">Juwelier Brenneck</div>
  <div class="letter__fold" style="top:212px"></div>
  <div class="letter__fold" style="top:423px"></div>
  <div class="letter__sender"><b>Juwelier Brenneck GmbH</b> | Lindenallee 12 | 45100 Beispielstadt</div>
  <div class="letter__address">Frau/Herr<span class="red">XY Mustermann</span>Musterstraße 1<div class="gap"></div><span class="red">12345 Musterstadt</span></div>
  <div class="letter__side">
    <div class="head">FILIALE</div><div class="red">Gartenweg 8<br>45200 Nebenstadt</div><b class="red">T</b> 0202 00 44 5<br><b class="red">F</b> 0202 00 55 66
    <div class="gap"></div>
    <div class="head red">KONTAKT</div><div class="red">Beispielstadt</div><b class="red">T</b> 0201 00 11 22<br><b class="red">F</b> 0201 00 11 33
    <div class="gap"></div>
    <b class="red">M</b> info@juwelier-brenneck-beispiel.de<br><b class="red">W</b> www.juwelier-brenneck-beispiel.de
  </div>
  <div class="letter__date">Beispielstadt, den 06. Mai 2014</div>
  <div class="letter__body">
    <p>Sehr geehrte Damen und Herren,<br>sehr geehrte/r Kunde/Kundin!</p>
    <p>Dus et re eatquidebita sim dolectur re nus, conseni hilita volorest rerovit es nam quatiis rerspidi berum reptiorum et ullorionet dolectatem alitat utem consent endae qui que nonsequatio imuscient aliquaecus derum simagniam dolor aditi blaborum ut fugia venient minumque dolum, volor simusa voluptae natiati sitatur, simetur maximusam que pror alias in reptat eum facepta nos re ant omnis ut fugiam inciam que autem dem sit, idus, quatio eos del in elenet quunt.</p>
    <p>Perferi onsequi nobis maio. Nam, sitas maxim aliquas suntibus, voluptis quo et rem nullor suntur, quo consequ aepudictatem nimilitaes ut as quae. Harupta volum enihiti doluptur re, eliquatur, tota velectur, sant, tecte nonserum, tet ut optatur maximagnate seruptaqui sunt alicipi denimus conecti untotat.<br>Evel mos simpore ruptate mquist, sus, omni aut quae porempo rehendanda vol.</p>
    <p>Otatur molupidel ipicidelibus eum qui qui tem fuga. Tiandit aturis et volorum quas nonestisquid eos soloreptate cullab ipsa cusandant alis et prerias dollige nitiorem ullat re cum et odio dempern atatescient.<br>Elestruntiis eos mo essin provit exerovidus exces nos eligene laborro volesciur si consequ istinus cilicatibus del maio. Namenis moluptatur, quas aut aut ut et volo-restior ratin reium quam doloresti nate nobitat uritione reicius autati doluptasimil magnimpor aperisquo te illabo. Nemperrumque porerumquod et excere pos molo-rendunt quis secabor rorepudit utecaectur?</p>
    <p class="close">Mit freundlichen Grüßen</p>
    <p>Juwelier Brenneck</p>
  </div>
  <div class="letter__foot"><b>JUWELIER BRENNECK GMBH</b> | Lindenallee 12 | 45100 Beispielstadt<br>Geschäftsführung <b>Marianne Brenneck</b> | Amtsgericht Musterstadt <b>HRB 00000</b> | Steuernummer <b>000/0000/0000</b> | USt.- ID <b>DE 000000000</b><br><b>BANK</b> Musterbank AG | <b>IBAN</b> DE00 0000 0000 0000 0000 00 | <b>BIC</b> MUST DE 0X</div>
</div>

<!-- compact letterhead pair -->
<div class="sheet letter" style="left:535px;top:427px;transform:scale(.69)">
  <div class="decor" role="img" aria-label="Große Diamant-Linienzeichnung in Grau" style="width:300px;height:440px;background:var(--tint-grey)"></div>
</div>
<div class="sheet letter letter--compact" style="left:485px;top:384px;transform:scale(.69)">
  <div class="brand">Juwelier Brenneck</div>
  <div class="letter__fold" style="top:155px"></div>
  <div class="letter__fold" style="top:400px"></div>
  <div class="letter__sender"><b>Juwelier Brenneck GmbH</b> | Lindenallee 12 | 45100 Beispielstadt</div>
  <div class="letter__address">Frau/Herr<span class="red">XY Mustermann</span>Musterstraße 1<div class="gap"></div><span class="red">12345 Musterstadt</span></div>
  <div class="letter__side">
    <div class="head">FILIALE</div><div class="red">Gartenweg 8<br>45200 Nebenstadt</div><b class="red">T</b> 0202 00 44 5<br><b class="red">F</b> 0202 00 55 66
    <div class="gap"></div>
    <div class="head red">KONTAKT</div><div class="red">Beispielstadt</div><b class="red">T</b> 0201 00 11 22<br><b class="red">F</b> 0201 00 11 33
    <div class="gap"></div>
    <b class="red">M</b> info@juwelier-brenneck-beispiel.de<br><b class="red">W</b> www.juwelier-brenneck-beispiel.de
  </div>
  <div class="letter__date">Beispielstadt, den 06. Mai 2014</div>
  <div class="letter__body">
    <p>Sehr geehrte Damen und Herren,<br>sehr geehrte/r Kunde/Kundin!</p>
    <p>Dus et re eatquidebita sim dolectur re nus, conseni hilita volorest rerovit es nam quatiis rerspidi berum reptiorum et ullorionet dolectatem alitat utem consent endae qui que nonsequatio imuscient aliquaecus derum simagniam dolor aditi blaborum ut fugia venient minumque dolum, volor simusa voluptae natiati sitatur, simetur maximusam que pror alias in reptat eum facepta nos re ant omnis ut fugiam inciam que autem dem sit, idus, quatio eos del in elenet quunt.</p>
    <p>Perferi onsequi nobis maio. Nam, sitas maxim aliquas suntibus, voluptis quo et rem nullor suntur, quo consequ aepudictatem nimilitaes ut as quae. Harupta volum enihiti doluptur re, eliquatur, tota velectur, sant, tecte nonserum, tet ut optatur maximagnate seruptaqui sunt alicipi denimus conecti untotat.<br>Evel mos simpore ruptate mquist, sus, omni aut quae porempo rehendanda vol.</p>
    <p>Otatur molupidel ipicidelibus eum qui qui tem fuga. Tiandit aturis et volorum quas nonestisquid eos soloreptate cullab ipsa cusandant alis et prerias dollige nitiorem ullat re cum et odio dempern atatescient.<br>Elestruntiis eos mo essin provit exerovidus exces nos eligene laborro volesciur si consequ istinus cilicatibus del maio. Namenis moluptatur, quas aut aut ut et volo-restior ratin reium quam doloresti nate nobitat uritione reicius autati doluptasimil magnimpor aperisquo te illabo. Nemperrumque porerumquod et excere pos molo-rendunt quis secabor rorepudit utecaectur?</p>
    <p class="close">Mit freundlichen Grüßen</p>
    <p>Juwelier Brenneck</p>
  </div>
  <div class="letter__foot"><b>JUWELIER BRENNECK GMBH</b> | Lindenallee 12 | 45100 Beispielstadt<br>Geschäftsführung <b>Marianne Brenneck</b> | Amtsgericht Musterstadt <b>HRB 00000</b> | Steuernummer <b>000/0000/0000</b> | USt.- ID <b>DE 000000000</b><br><b>BANK</b> Musterbank AG | <b>IBAN</b> DE00 0000 0000 0000 0000 00 | <b>BIC</b> MUST DE 0X</div>
</div>

<!-- standalone brand name -->
<div class="brand" style="position:absolute;left:600px;top:1085px;width:235px;font-size:20px">Juwelier Brenneck</div>

</body>
</html>
```